School Poster

Design so that these can be placed in classrooms across the school.

Attached is another design we have had done. Use a similar theme.

Consider using themes from https://corvalhs.edq.example.au/

please edit Binder1 doc.

Students and teachers

```html
<!DOCTYPE html>
<html lang="en">
<head>
<meta charset="utf-8">
<title>Classroom Posters – Corval SHS</title>
<link href="https://fonts.googleapis.com/css2?family=Poppins:wght@400;500;600;700;800&display=swap" rel="stylesheet">
<style>
:root{
  --stage:#d8d9d8;
  --blue:#2f4b9b;
  --navy:#233c8c;
  --yellow:#f3ea7c;
  --grey:#e7e8e8;
  --white:#ffffff;
  --ink:#1f2a44;
  --red:#d3262b;
  --text:#2b2f3a;
}
*{box-sizing:border-box;margin:0;padding:0}
html,body{width:1200px;height:960px;overflow:hidden}
body{background:var(--stage);font-family:'Poppins',sans-serif;color:var(--text);position:relative}
.poster{position:absolute;top:144px;width:476px;height:672px;background:var(--blue);overflow:hidden}
.poster--help{left:106px}
.poster--ai{left:618px}
.poster__header{position:absolute;left:0;top:0;width:100%;height:101px;background:var(--blue)}
.poster__title{position:absolute;left:23px;top:22px;width:350px;color:var(--white);font-weight:800;font-size:32px;line-height:32px;letter-spacing:0;text-transform:uppercase;white-space:nowrap}
.school-mark{position:absolute;right:22px;top:22px;width:62px;display:flex;flex-direction:column;align-items:center;gap:6px;color:var(--white);font-weight:800;font-size:12px;line-height:13px;text-align:center}
.school-mark__dot{width:34px;height:34px;background:var(--yellow)}
.tagline{position:absolute;left:0;top:101px;width:100%;height:29px;background:var(--yellow);padding-left:24px;font-size:21px;line-height:29px;color:var(--ink);font-weight:400}
.poster--help .poster__foot{position:absolute;left:0;top:612px;width:100%;height:60px;background:var(--yellow)}
.card{position:absolute;left:9.5px;width:457px;background:var(--white);border-radius:7px}
.poster--help .card{top:141px;height:471px}
.step{position:absolute;top:25px;width:137px;height:418px;border:2.5px solid var(--navy);border-radius:9px;background:var(--white)}
.step:nth-child(1){left:14px}.step:nth-child(2){left:160px}.step:nth-child(3){left:306px}
.step__num{position:absolute;left:50%;top:-15px;transform:translateX(-50%);width:26px;height:26px;border-radius:50%;background:var(--navy);color:var(--white);font-weight:800;font-size:17px;line-height:26px;text-align:center;box-shadow:0 0 0 4px var(--white)}
.step__art{position:absolute;left:24px;top:25px;width:84px;height:86px;border-radius:10px;background:linear-gradient(160deg,#3a56a8,#2a448f 60%,#f3e25a)}
.step__name{position:absolute;left:0;top:118px;width:100%;height:74px;display:flex;align-items:center;justify-content:center;text-align:center;color:var(--navy);font-weight:800;font-size:19px;line-height:19px;text-transform:uppercase}
.step__lead{position:absolute;left:0;top:192px;width:100%;height:46px;background:var(--yellow);display:flex;align-items:center;justify-content:center;text-align:center;color:var(--navy);font-weight:700;font-size:12px;line-height:13px;padding:0 6px}
.step__body{position:absolute;left:0;top:238px;width:100%;bottom:0;background:var(--grey);border-radius:0 0 7px 7px;padding:8px 8px 0 12px}
.step__list{list-style:none}
.step__list li{position:relative;padding-left:12px;font-size:10px;line-height:14.5px;margin-bottom:3.5px}
.step__list li::before{content:"";position:absolute;left:0;top:5px;width:4px;height:4px;border-radius:50%;background:var(--navy)}
.step__then{font-weight:700;font-size:9.6px;line-height:14.5px;margin-top:1px;color:var(--ink)}
.value-pill{position:absolute;left:50%;bottom:-14px;transform:translateX(-50%);width:112px;height:26px;border-radius:6px;background:var(--navy);color:var(--white);font-weight:800;font-size:15px;line-height:26px;text-align:center;white-space:nowrap;box-shadow:0 0 0 3px var(--white)}
.value-pill b{color:var(--yellow);font-weight:800}
.references{position:absolute;left:15px;top:624px;width:450px;font-size:5.2px;line-height:6px;color:#333}
.references strong{display:block;font-size:5.4px}

.ai-stripe{position:absolute;left:0;top:101px;width:100%;height:9px;background:var(--yellow)}
.poster--ai .card{top:131px;height:506px}
.section-title{position:absolute;left:0;width:100%;text-align:center;color:var(--navy);font-weight:800;font-size:19.5px;line-height:20px;text-transform:uppercase}
.must-list{position:absolute;list-style:none}
.must-list li{position:relative;padding-left:15px;font-weight:600;font-size:10.8px;line-height:13.8px;color:var(--ink);margin-bottom:4px}
.must-list svg{position:absolute;left:0;top:3px;width:8px;height:8px}
.must-list--left{left:22px;top:40px;width:182px}
.must-list--right{left:208px;top:40px;width:124px}
.ai-art{position:absolute;left:338px;top:23px;width:106px;height:108px;border-radius:50%;background:radial-gradient(circle at 45% 50%,#ffffff 20%,#dfe4f3 55%,#f6f0b0)}
.help-box{position:absolute;left:14.5px;top:138px;width:427px;height:197px;background:var(--yellow);border-radius:8px}
.help-box .section-title{top:10px}
.help-box__note{position:absolute;top:31px;width:100%;text-align:center;font-size:12px;color:var(--navy)}
.tiles{position:absolute;left:0;top:58px;width:100%;height:130px;display:flex}
.tile{flex:1;position:relative;border-left:1px solid #8c8a63}
.tile:first-child{border-left:none}
.tile__art{width:58px;height:64px;margin:0 auto;border-radius:8px;background:linear-gradient(160deg,#2f4b9b,#233c8c 70%,#f3ea7c)}
.tile__label{margin-top:15px;text-align:center;color:var(--navy);font-weight:700;font-size:11.2px;line-height:12.8px;padding:0 4px}
.cannot{position:absolute;left:14.5px;top:380px;width:427px;height:124px;display:flex}
.cannot__item{flex:1;border-left:1px solid #bdbdbd;text-align:center}
.cannot__item:first-child{border-left:none}
.cannot__item svg{width:38px;height:38px;display:block;margin:0 auto}
.cannot__item p{margin-top:8px;font-weight:700;font-size:11.2px;line-height:12.8px;color:var(--ink);padding:0 5px}
.ai-footer{position:absolute;left:0;top:647px;width:100%;text-align:center;color:var(--white);font-weight:700;font-size:11.3px}
</style>
</head>
<body>

<section class="poster poster--help">
  <header class="poster__header">
    <h1 class="poster__title">Before you ask<br>the teacher...</h1>
    <div class="school-mark"><span class="school-mark__dot"></span>Corval SHS</div>
  </header>
  <p class="tagline">TRY THESE STEPS FIRST!</p>
  <div class="poster__foot"></div>
  <div class="card">
    <article class="step">
      <span class="step__num">1</span>
      <div class="step__art" role="img" aria-label="Icon of a head with a lightbulb"></div>
      <h2 class="step__name">Think<br>First</h2>
      <p class="step__lead">Don't give up straight away.</p>
      <div class="step__body">
        <ul class="step__list">
          <li>Read the question carefully.</li>
          <li>Identify what you already know.</li>
          <li>Try a strategy you've used before.</li>
          <li>Give yourself thinking time.</li>
        </ul>
      </div>
      <span class="value-pill">WE <b>BELIEVE</b></span>
    </article>
    <article class="step">
      <span class="step__num">2</span>
      <div class="step__art" role="img" aria-label="Icon of a clipboard checklist"></div>
      <h2 class="step__name">Check<br>your<br>supports</h2>
      <p class="step__lead">Before asking for help, check:</p>
      <div class="step__body">
        <ul class="step__list">
          <li>Learning goal and success criteria.</li>
          <li>Worked examples.</li>
          <li>Class notes.</li>
          <li>Classroom displays.</li>
          <li>LearnHub resources.</li>
          <li>Task sheet and instructions.</li>
        </ul>
      </div>
      <span class="value-pill">WE <b>STRIVE</b></span>
    </article>
    <article class="step">
      <span class="step__num">3</span>
      <div class="step__art" role="img" aria-label="Icon of a group with speech bubbles"></div>
      <h2 class="step__name">Ask 3<br>before me</h2>
      <p class="step__lead">Ask three sources before asking the teacher:</p>
      <div class="step__body">
        <ul class="step__list">
          <li>A person (partner or neighbour)</li>
          <li>A place (notes, display, LearnHub)</li>
          <li>A resource (worked example, task sheet)</li>
        </ul>
        <p class="step__then">Then ask the teacher if you still need help.</p>
      </div>
      <span class="value-pill">WE <b>ACHIEVE</b></span>
    </article>
  </div>
  <div class="references">
    <strong>References</strong>
    Harlow, M. (2025). Why Students Don't Ask for Help – And How to Change That. Downloaded 24/04/2026 from: https://learnwell.example.org/article/asking-for-help/<br><br>
    ERLO. (2024). Supporting Self-Regulated Learning. Downloaded 24/04/2026 from: https://evidencehub.example.au/files/2024-02/self-regulated-learning.pdf
  </div>
</section>

<section class="poster poster--ai">
  <header class="poster__header">
    <h1 class="poster__title">Using AI and other<br>tools responsibly</h1>
    <div class="school-mark"><span class="school-mark__dot"></span>Corval SHS</div>
  </header>
  <div class="ai-stripe"></div>
  <div class="card">
    <h2 class="section-title" style="top:9px">What you must do:</h2>
    <ul class="must-list must-list--left">
      <li><svg viewBox="0 0 8 8"><rect x=".5" y=".5" width="7" height="7" fill="none" stroke="#233c8c"/><path d="M1.8 4l1.5 1.6L6.3 2" fill="none" stroke="#233c8c" stroke-width="1"/></svg>Complete your own work</li>
      <li><svg viewBox="0 0 8 8"><rect x=".5" y=".5" width="7" height="7" fill="none" stroke="#233c8c"/><path d="M1.8 4l1.5 1.6L6.3 2" fill="none" stroke="#233c8c" stroke-width="1"/></svg>Demonstrate your progress (drafts, notes, planning, revisions)</li>
      <li><svg viewBox="0 0 8 8"><rect x=".5" y=".5" width="7" height="7" fill="none" stroke="#233c8c"/><path d="M1.8 4l1.5 1.6L6.3 2" fill="none" stroke="#233c8c" stroke-width="1"/></svg>Use feedback to improve your work</li>
    </ul>
    <ul class="must-list must-list--right">
      <li><svg viewBox="0 0 8 8"><rect x=".5" y=".5" width="7" height="7" fill="none" stroke="#233c8c"/><path d="M1.8 4l1.5 1.6L6.3 2" fill="none" stroke="#233c8c" stroke-width="1"/></svg>Demonstrate your understanding of the ideas in your submission</li>
    </ul>
    <div class="ai-art" role="img" aria-label="Illustration of a brain joined to an AI circuit"></div>

    <div class="help-box">
      <h2 class="section-title">What AI can help you do</h2>
      <p class="help-box__note">(when approved by your teacher)</p>
      <div class="tiles">
        <div class="tile"><div class="tile__art" role="img" aria-label="Brain icon"></div><p class="tile__label">Brainstorm ideas</p></div>
        <div class="tile"><div class="tile__art" role="img" aria-label="Checklist with magnifier icon"></div><p class="tile__label">Check spelling, grammar and clarity</p></div>
        <div class="tile"><div class="tile__art" role="img" aria-label="Phone with audio wave icon"></div><p class="tile__label">Read your work aloud using text-to-speech tools</p></div>
        <div class="tile"><div class="tile__art" role="img" aria-label="Rising bar chart with gear icon"></div><p class="tile__label">Help identify areas for improvement in a draft</p></div>
      </div>
    </div>

    <h2 class="section-title" style="top:346px">What you cannot do:</h2>
    <div class="cannot">
      <div class="cannot__item"><svg viewBox="0 0 40 40"><path d="M33 12A16 16 0 1 0 36 22" fill="none" stroke="#d3262b" stroke-width="3.4" stroke-linecap="round"/><path d="M14 13l12 15M26 13L14 28" stroke="#d3262b" stroke-width="3.4" stroke-linecap="round"/></svg><p>Submit AI-generated work as your own</p></div>
      <div class="cannot__item"><svg viewBox="0 0 40 40"><path d="M33 12A16 16 0 1 0 36 22" fill="none" stroke="#d3262b" stroke-width="3.4" stroke-linecap="round"/><path d="M14 13l12 15M26 13L14 28" stroke="#d3262b" stroke-width="3.4" stroke-linecap="round"/></svg><p>Copy and paste AI responses without acknowledging or adapting them</p></div>
      <div class="cannot__item"><svg viewBox="0 0 40 40"><path d="M33 12A16 16 0 1 0 36 22" fill="none" stroke="#d3262b" stroke-width="3.4" stroke-linecap="round"/><path d="M14 13l12 15M26 13L14 28" stroke="#d3262b" stroke-width="3.4" stroke-linecap="round"/></svg><p>Use AI tools to complete the whole task for you</p></div>
      <div class="cannot__item"><svg viewBox="0 0 40 40"><path d="M33 12A16 16 0 1 0 36 22" fill="none" stroke="#d3262b" stroke-width="3.4" stroke-linecap="round"/><path d="M14 13l12 15M26 13L14 28" stroke="#d3262b" stroke-width="3.4" stroke-linecap="round"/></svg><p>Submit work that does not demonstrate your understanding</p></div>
    </div>
  </div>
  <p class="ai-footer">If you didn't create, develop and understand it, it isn't your work.</p>
</section>

</body>
</html>
```